Hi Designers,

I will need 4 web pages designed. The web page looks like an App (if you click on the logo, or the icon on an iPad, it will take you to the website), but it is still a webpage.

Please check the attachment on this brief to understand what specific pages I need to be designed.

A .PSD (straight-up PhotoShop image) as final deliverable is fine, as long as you give us the exact “web color numbers”.

The design is for desktop and iPad but in a single unified web application, NOT separate web app and (native) iPad app.

Details:

Brightwater Policy Partners is developing a browser-based application for use on any mobile device or desktop. The app will be used by corporations to communicate with their employees regarding legal, regulatory and company requirements for conducting business. The app is known as “Harbor Guidance Portal.” When the user clicks on the icon for Harbor Guidance Portal, they will enter a site full of information that a company deems necessary for the employee to do his/her job. There are several content sections within the site, including a login page, training, policies, forms, news feeds and blogs.

The application has been built using Microsoft .NET, and fully supports CSS-type skinning; it uses traditional page layouts. We are seeking a product logo concept (image), a master application/desktop icon (image), as well as a full color scheme/theme/skin design for all areas of the application (header area, body text, menu bar, etc.) in the form of a CSS. The look should be clean, crisp and professional; nothing cartoony or whimsical. It should be easy to read and “airy”.

We have sketched prototypes for the basic application page layout that we can send as a next step of the process.
Updates

Screen shots have been uploaded to this project.  Please use them to guide your design.

Dear designers,

I apologize for the delay in providing feedback. My partners and I will provide feedback in a few days. Thank you for your patience.

Industry/Entity Type

Business

Font styles to use
Other font styles liked:
• see font on screen shots when uploaded

```html
<!DOCTYPE html>
<html lang="en">
<head>
<meta charset="utf-8">
<title>Harbor Guidance Portal</title>
<link rel="stylesheet" href="https://fonts.googleapis.com/css2?family=Source+Sans+3:wght@400;600&display=swap">
<style>
:root{
  --blue:#3a9be8;
  --blue-dark:#1c6bb5;
  --link:#1e88d6;
  --text:#4a4a4a;
  --muted:#666;
  --line:#dcdcdc;
  --panel-border:#e2e2e2;
  --header-top:#f7f7f7;
  --header-bottom:#e4e4e4;
  --gold:#f9c100;
  --gold-dark:#eaa800;
  --row:#efefef;
  --footer:#0d0d0d;
}
*{box-sizing:border-box;margin:0;padding:0}
html,body{width:1200px;height:1099px;overflow:hidden}
body{font-family:"Source Sans 3",sans-serif;color:var(--text);background:#fff;position:relative}
.abs{position:absolute}

/* header */
.site-header{position:absolute;left:0;top:0;width:1200px;height:83px;background:linear-gradient(var(--header-top),var(--header-bottom));border-bottom:1px solid #d6d6d6}
.brand-mark{left:60px;top:22px;width:36px;height:40px;border-radius:50%;background:#1aa0dd}
.brand-name{left:116px;top:17px;font-size:16px;line-height:30px;color:#444}
.nav-item{top:12px;width:80px;text-align:center;font-size:13px;color:#666}
.nav-item svg{display:block;margin:0 auto 6px}
.nav-item.active{color:var(--link)}
.search{height:29px;border:1px solid #cfcfcf;background:#fff;font-size:13px;color:#888;padding:6px 11px;display:flex;justify-content:space-between;align-items:center}
.score-badge{left:888px;top:0;width:80px;height:57px;background:linear-gradient(var(--gold),var(--gold-dark))}
.score-badge .points{left:24px;top:8px;font-size:19px;color:#7a5a00}
.count-dot{width:24px;height:24px;border-radius:50%;background:var(--blue-dark);color:#fff;border:2px solid #fff;font-size:15px;text-align:center;line-height:20px}
.avatar{left:1008px;top:16px;width:46px;height:41px;background:linear-gradient(#d8c3a8,#5a4a3e)}
.user-name{left:1067px;top:31px;font-size:14px;color:#555}

/* panels */
.panel{position:absolute;background:#fff;border:3px solid #f0f0f0;box-shadow:0 0 0 1px var(--panel-border) inset}
.panel-title{font-size:20px;color:var(--blue-dark);font-weight:400}
.bar-head{height:50px;background:var(--blue);color:#fff;font-size:17px;display:flex;align-items:center;padding-left:14px;gap:20px}

/* news */
.news-item{position:absolute;left:12px;width:240px;height:104px;border-bottom:1px solid var(--line)}
.calendar{position:absolute;left:0;top:0;width:52px;height:44px;background:#ececec}
.calendar .rings{height:11px;background:var(--blue);position:relative}
.calendar .rings i{position:absolute;top:-3px;width:3px;height:7px;background:#fff;border-radius:2px}
.calendar .day{font-size:13px;color:#333;text-align:center;margin-top:6px}
.calendar .fold{position:absolute;right:6px;bottom:0;border-style:solid;border-width:0 0 8px 8px;border-color:transparent transparent #999 transparent}
.news-text{position:absolute;left:68px;top:0;font-size:13px;line-height:22px;color:#333;width:175px}
.news-link{position:absolute;left:0;top:55px;font-size:13px;color:var(--link)}

/* what's new */
.update{position:absolute;left:8px;width:242px;height:89px;border-bottom:1px solid var(--line)}
.thumb{position:absolute;left:0;top:0;width:78px;height:52px}
.update h3{position:absolute;left:88px;top:-3px;font-size:13px;font-weight:400;color:var(--link);white-space:nowrap}
.update p{position:absolute;left:88px;top:16px;font-size:13px;line-height:21px;color:var(--muted);width:160px}

/* game center */
.game-card{position:absolute;left:15px;width:227px;height:61px;border:1px solid #ccc;border-radius:2px}
.game-card p{position:absolute;left:69px;top:10px;font-size:13px;line-height:21px;color:#444}
.play-btn{position:absolute;left:57px;top:351px;width:141px;height:34px;background:var(--blue);color:#fff;font-size:15px;text-align:center;line-height:34px}

/* leaderboard */
.board-head{height:51px;background:linear-gradient(var(--gold),var(--gold-dark));color:#fff;font-size:20px;padding:12px 0 0 14px}
.view-all{position:absolute;left:9px;top:64px;width:204px;height:41px;border:1px solid #ccc;font-size:15px;text-align:center;line-height:39px;color:#444;background:#fff}
.board-cols{position:absolute;top:126px;font-size:15px;color:#444}
.board-row{position:absolute;left:3px;width:216px;height:48px;background:var(--row);font-size:13px;color:#555}
.rank{position:absolute;left:10px;top:10px;width:27px;height:27px;border-radius:50%;background:#d8d8d8;font-size:15px;text-align:center;line-height:27px;color:#555}
.board-row span{position:absolute;top:16px}
.quick-links{position:absolute;left:0;bottom:0;width:100%;height:31px;background:#555;color:#fff;font-size:14px;text-align:center;line-height:31px}

/* footer */
.site-footer{position:absolute;left:0;top:1012px;width:1200px;height:87px;background:var(--footer);color:#ddd;font-size:12px}
.social{position:absolute;top:28px;width:30px;height:30px}
</style>
</head>
<body>

<header class="site-header">
  <div class="abs brand-mark"></div>
  <div class="abs brand-name">Harbor Guidance<br>Portal</div>

  <div class="abs nav-item active" style="left:276px">
    <svg width="32" height="32" viewBox="0 0 32 32"><path d="M16 2 1 16h4v14h8v-9h6v9h8V16h4z" fill="#2f86d0"/></svg>HOME</div>
  <div class="abs nav-item" style="left:362px">
    <svg width="32" height="32" viewBox="0 0 32 32" fill="#8a8a8a"><rect x="2" y="2" width="8" height="8"/><rect x="12" y="2" width="8" height="8"/><rect x="22" y="2" width="8" height="8"/><rect x="2" y="12" width="8" height="8"/><rect x="12" y="12" width="8" height="8"/><rect x="22" y="12" width="8" height="8"/><rect x="2" y="22" width="8" height="8"/><rect x="12" y="22" width="8" height="8"/><rect x="22" y="22" width="8" height="8"/></svg>MENU</div>
  <div class="abs nav-item" style="left:448px">
    <svg width="32" height="32" viewBox="0 0 32 32"><path d="M4 2h24v28H4z" fill="#8a8a8a"/><path d="M8 2h6v14l-3-3-3 3z" fill="#fff"/></svg>GAME</div>
  <div class="abs nav-item" style="left:540px">
    <svg width="32" height="32" viewBox="0 0 32 32" fill="#8a8a8a"><circle cx="6" cy="16" r="5"/><circle cx="26" cy="5" r="5"/><circle cx="26" cy="27" r="5"/><path d="M6 16 26 5M6 16l20 11" stroke="#8a8a8a" stroke-width="3"/></svg>HCP SEC</div>

  <div class="abs search" style="left:640px;top:28px;width:217px">Search..
    <svg width="12" height="12" viewBox="0 0 12 12"><circle cx="5" cy="5" r="4" fill="none" stroke="#888" stroke-width="1.6"/><path d="M8 8l3.5 3.5" stroke="#888" stroke-width="1.6"/></svg></div>

  <div class="abs score-badge"><span class="abs points">427</span><span class="abs count-dot" style="left:47px;top:33px">1</span></div>
  <div class="abs avatar" role="img" aria-label="User profile photo"></div>
  <div class="abs user-name">Sam Carter</div>
</header>

<!-- Industry News -->
<section class="panel" style="left:62px;top:116px;width:272px;height:842px">
  <h2 class="abs panel-title" style="left:12px;top:12px">Industry News</h2>
  <div class="abs search" style="left:13px;top:54px;width:237px;height:30px">Search..
    <svg width="12" height="12" viewBox="0 0 12 12"><circle cx="5" cy="5" r="4" fill="none" stroke="#888" stroke-width="1.6"/><path d="M8 8l3.5 3.5" stroke="#888" stroke-width="1.6"/></svg></div>

  <article class="news-item" style="top:109px"><div class="calendar"><div class="rings"><i style="left:9px"></i><i style="left:24px"></i><i style="left:39px"></i></div><div class="day">Oct 12</div><b class="fold"></b></div><p class="news-text">Nam liber tempor cum solutan obis eleifend option congue.</p><a class="news-link">Agency News : Typi non habent claritat</a></article>
  <article class="news-item" style="top:212px"><div class="calendar"><div class="rings"><i style="left:9px"></i><i style="left:24px"></i><i style="left:39px"></i></div><div class="day">Nov 13</div><b class="fold"></b></div><p class="news-text">Nam liber tempor cum solutan obis eleifend option congue.</p><a class="news-link">Agency News : Typi non habent claritat</a></article>
  <article class="news-item" style="top:317px"><div class="calendar"><div class="rings"><i style="left:9px"></i><i style="left:24px"></i><i style="left:39px"></i></div><div class="day">Nov 13</div><b class="fold"></b></div><p class="news-text">Nam liber tempor cum solutan obis eleifend option congue.</p><a class="news-link">Agency News : Typi non habent claritat</a></article>
  <article class="news-item" style="top:420px"><div class="calendar"><div class="rings"><i style="left:9px"></i><i style="left:24px"></i><i style="left:39px"></i></div><div class="day">Nov 13</div><b class="fold"></b></div><p class="news-text">Nam liber tempor cum solutan obis eleifend option congue.</p><a class="news-link">Agency News : Typi non habent claritat</a></article>
  <article class="news-item" style="top:523px"><div class="calendar"><div class="rings"><i style="left:9px"></i><i style="left:24px"></i><i style="left:39px"></i></div><div class="day">Nov 13</div><b class="fold"></b></div><p class="news-text">Nam liber tempor cum solutan obis eleifend option congue.</p><a class="news-link">Agency News : Typi non habent claritat</a></article>
  <article class="news-item" style="top:627px"><div class="calendar"><div class="rings"><i style="left:9px"></i><i style="left:24px"></i><i style="left:39px"></i></div><div class="day">Nov 13</div><b class="fold"></b></div><p class="news-text">Nam liber tempor cum solutan obis eleifend option congue.</p><a class="news-link">Agency News : Typi non habent claritat</a></article>
  <article class="news-item" style="top:731px;border-bottom:0"><div class="calendar"><div class="rings"><i style="left:9px"></i><i style="left:24px"></i><i style="left:39px"></i></div><div class="day">Nov 13</div><b class="fold"></b></div><p class="news-text">Nam liber tempor cum solutan obis eleifend option congue.</p><a class="news-link">Agency News : Typi non habent claritat</a></article>
</section>

<!-- Welcome -->
<section class="panel" style="left:349px;top:117px;width:542px;height:130px">
  <h1 class="abs" style="left:14px;top:13px;font-size:16px;font-weight:400;color:var(--blue-dark)">Welcome to Harbor Guidance Portal</h1>
  <div class="abs" role="img" aria-label="Photo of a plaza with a mural" style="left:15px;top:49px;width:81px;height:55px;background:linear-gradient(#6f8fb8,#3c5d8a 60%,#4c6a3a)"></div>
  <p class="abs" style="left:112px;top:45px;width:414px;font-size:13px;line-height:21px;color:#555">Typi non habent claritatem insitam; est usus legentis in iis qui facit eorum c laritatem. Investigationes demonstraverunt lectores legere me lius quodiile gunt saepius. Claritas est etiam processus dynamicus, qui sequitur mutat.</p>
</section>

<!-- What's New -->
<section class="panel" style="left:349px;top:268px;width:264px;height:690px;border-top:0">
  <div class="bar-head"><svg width="24" height="24" viewBox="0 0 24 24"><path d="M12 1l3.3 7 7.7.8-5.8 5.2 1.7 7.6L12 17.7l-6.9 3.9 1.7-7.6L1 8.8 8.7 8z" fill="#fff"/></svg>What’ s New?</div>
  <article class="update" style="top:69px"><div class="thumb" role="img" aria-label="Photo of a riverside city walkway" style="background:linear-gradient(#9db8d6,#6f7f8c 60%,#4a5560)"></div><h3>Code of conduct certificaton</h3><p>Typi non habent clariatem in sitam; est usus legentis inis.</p></article>
  <article class="update" style="top:158px"><div class="thumb" role="img" aria-label="Photo of a modern building" style="background:linear-gradient(#c9d6e2,#8a9098 60%,#6b6f70)"></div><h3>Code of conduct certificaton</h3><p>Typi non habent clariatem in sitam; est usus legentis inis.</p></article>
  <article class="update" style="top:245px"><div class="thumb" role="img" aria-label="Photo of a brick house" style="background:linear-gradient(#a9c4e0,#9a5a44 55%,#5e6b4a)"></div><h3>Code of conduct certificaton</h3><p>Typi non habent clariatem in sitam; est usus legentis inis.</p></article>
  <article class="update" style="top:333px"><div class="thumb" role="img" aria-label="Photo of a town hall under blue sky" style="background:linear-gradient(#7ea6d8,#c9d4e2 45%,#8a5a4a 70%,#777)"></div><h3>Code of conduct certificaton</h3><p>Typi non habent clariatem in sitam; est usus legentis inis.</p></article>
  <article class="update" style="top:422px"><div class="thumb" role="img" aria-label="Photo of a handshake" style="background:linear-gradient(135deg,#7a3b2a,#d9b7a0 55%,#eee)"></div><h3>Code of conduct certificaton</h3><p>Typi non habent clariatem in sitam; est usus legentis inis.</p></article>
  <article class="update" style="top:512px"><div class="thumb" role="img" aria-label="Photo of people in a meeting" style="background:linear-gradient(135deg,#2a2622,#6b5a48 60%,#3a342e)"></div><h3>Code of conduct certificaton</h3><p>Typi non habent clariatem in sitam; est usus legentis inis.</p></article>
  <article class="update" style="top:602px;border-bottom:0"><div class="thumb" role="img" aria-label="Photo of a crowd at an event" style="background:linear-gradient(135deg,#5a3a3a,#b08a6a 50%,#4a3a4a)"></div><h3>Code of conduct certificaton</h3><p>Typi non habent clariatem in sitam; est usus legentis inis.</p></article>
</section>

<!-- Compliance Game Center -->
<section class="panel" style="left:628px;top:268px;width:264px;height:690px;border-top:0">
  <div class="bar-head"><svg width="24" height="24" viewBox="0 0 24 24"><path d="M1 2h22v20l-11-6-11 6z" fill="#fff"/></svg>Compliance Game Center</div>
  <p class="abs" style="left:0;top:65px;width:100%;text-align:center;font-size:13px;color:var(--link)">Know your way around the center</p>
  <div class="game-card" style="top:110px">
    <svg class="abs" style="left:10px;top:8px" width="46" height="46" viewBox="0 0 46 46" fill="none" stroke="#777" stroke-width="2"><path d="M3 3h20l6 6v20H3z"/><path d="M17 17h20l6 6v20H17z" fill="#fff"/><path d="M8 16h10m-4-4 4 4-4 4M38 30H26m4-4-4 4 4 4"/></svg>
    <p>Typi non habent claritatem<br>insitam; est usus legentis</p></div>
  <div class="game-card" style="top:190px">
    <div class="abs" style="left:12px;top:13px;width:34px;height:25px;background:var(--gold);font-size:12px;color:#6a4d00;padding:3px 0 0 6px">427</div>
    <span class="abs count-dot" style="left:34px;top:26px;width:22px;height:22px;font-size:13px;line-height:18px">1</span>
    <p>Typi non habent claritatem<br>insitam; est usus legentis</p></div>
  <div class="game-card" style="top:268px">
    <svg class="abs" style="left:18px;top:12px" width="22" height="20" viewBox="0 0 22 20" fill="#777"><rect x="0" y="0" width="6" height="5"/><rect x="8" y="0" width="6" height="5"/><rect x="16" y="0" width="6" height="5"/><rect x="0" y="7" width="6" height="5"/><rect x="8" y="7" width="6" height="5"/><rect x="16" y="7" width="6" height="5"/><rect x="0" y="14" width="6" height="5"/><rect x="8" y="14" width="6" height="5"/><rect x="16" y="14" width="6" height="5"/></svg>
    <span class="abs" style="left:17px;top:38px;font-size:10px;color:#555">Menu</span>
    <p>Typi non habent claritatem<br>insitam; est usus legentis</p></div>
  <a class="play-btn">PLAY THE GAME</a>
</section>

<!-- Leaderboard -->
<section class="panel" style="left:906px;top:117px;width:228px;height:841px;border:0;box-shadow:0 0 0 1px var(--panel-border) inset">
  <div class="board-head">Leaderboard</div>
  <div class="view-all">View all Player Scores</div>
  <span class="board-cols" style="left:15px">Rank</span>
  <span class="board-cols" style="left:71px">Player</span>
  <span class="board-cols" style="left:129px">%</span>
  <span class="board-cols" style="left:160px">Score</span>

  <div class="board-row" style="top:160px"><b class="rank">4</b><span style="left:66px">Carter</span><span style="left:125px">88</span><span style="left:165px">426</span></div>
  <div class="board-row" style="top:210px"><b class="rank">5</b><span style="left:66px">Carter</span><span style="left:125px">88</span><span style="left:165px">426</span></div>
  <div class="board-row" style="top:260px"><b class="rank">6</b><span style="left:66px">Carter</span><span style="left:125px">88</span><span style="left:165px">426</span></div>
  <div class="board-row" style="top:310px"><b class="rank">7</b><span style="left:66px">Carter</span><span style="left:125px">88</span><span style="left:165px">426</span></div>
  <div class="board-row" style="top:360px"><b class="rank">8</b><span style="left:66px">Carter</span><span style="left:125px">88</span><span style="left:165px">426</span></div>
  <div class="board-row" style="top:410px"><b class="rank">9</b><span style="left:66px">Carter</span><span style="left:125px">88</span><span style="left:165px">426</span></div>
  <div class="board-row" style="top:460px"><b class="rank">10</b><span style="left:66px">Carter</span><span style="left:125px">88</span><span style="left:165px">426</span></div>
  <div class="board-row" style="top:510px"><b class="rank">11</b><span style="left:66px">Carter</span><span style="left:125px">88</span><span style="left:165px">426</span></div>
  <div class="board-row" style="top:560px"><b class="rank">12</b><span style="left:66px">Carter</span><span style="left:125px">88</span><span style="left:165px">426</span></div>
  <div class="board-row" style="top:610px"><b class="rank">13</b><span style="left:66px">Carter</span><span style="left:125px">88</span><span style="left:165px">426</span></div>
  <div class="board-row" style="top:660px"><b class="rank">14</b><span style="left:66px">Carter</span><span style="left:125px">88</span><span style="left:165px">426</span></div>
  <div class="board-row" style="top:710px"><b class="rank">15</b><span style="left:66px">Carter</span><span style="left:125px">88</span><span style="left:165px">426</span></div>
  <div class="board-row" style="top:760px"><b class="rank">16</b><span style="left:66px">Carter</span><span style="left:125px">88</span><span style="left:165px">426</span></div>
  <div class="quick-links">Quick Links</div>
</section>

<footer class="site-footer">
  <p class="abs" style="left:72px;top:22px">Terms and conditions | Privacy Policy</p>
  <p class="abs" style="left:72px;top:50px">Copyright 2013.  All rights reserved.</p>
  <a class="social" aria-label="Social link" style="left:820px;background:#2f56a8"></a>
  <a class="social" aria-label="Social link" style="left:861px;background:#2a98d8"></a>
  <a class="social" aria-label="Feed link" style="left:902px;background:#f26a1b"></a>
  <a class="social" aria-label="Video link" style="left:943px;background:#c8171e"></a>
</footer>

</body>
</html>
```